ambitious event and festival agency from austria needs fresh business card design

A new design is due for the new headquarters and the new challenges. We organize events for different target groups from 16 to 60 years. The design should therefore be straightforward and not confused, so we are open to new colors and the logo may also be changed. In general, however, the most interesting suggestions are the most interesting ones. after this order we are looking for more graphics for ravelmere facebook instagramm homepage etc A new design is due for the new headquarters and the new challenges. We organize events for different target groups from 16 to 60 years. The design should therefore be straightforward and not confused, so we are open to new colors and the logo may also be changed. In general, however, the most interesting suggestions are the most interesting ones. after this order we are looking for more graphics for ravelmere facebook instagramm homepage etc A new design is due for the new headquarters and the new challenges. We organize events for different target groups from 16 to 60 years. The design should therefore be straightforward and not confused, so we are open to new colors and the logo may also be changed. In general, however, the most interesting suggestions are the most interesting ones. after this order we are looking for more graphics for ravelmere facebook instagramm homepage etc
Updates

Reason: I am sorry for this decision but i need some more time. No new designs please, there are so many good ones and I will have made a decision in the next 3 days.

Target Market(s)

Industry/Entity Type

Business

Font styles to use
Serif
Sans Serif

Colors

Designer to choose colors to be used in the design.

Requirements
Must have
Nice to have
Should not have

```html
<!DOCTYPE html>
<html lang="de">
<head>
<meta charset="utf-8">
<title>ravelmere – Visitenkarte</title>
<link href="https://fonts.googleapis.com/css2?family=Roboto:wght@300;400;500;700&display=swap" rel="stylesheet">
<style>
  :root {
    --stage: #3a3a3d;
    --card: #222224;
    --accent: #e0334f;
    --muted: #8a8c8e;
    --text: #f2f2f2;
    --divider: #9a9a9c;
  }
  * { box-sizing: border-box; margin: 0; padding: 0; }
  html, body { width: 1200px; height: 900px; overflow: hidden; }
  body {
    background: var(--stage);
    font-family: "Roboto", Arial, sans-serif;
    color: var(--text);
    display: flex;
    flex-direction: column;
    align-items: center;
    justify-content: center;
    gap: 40px;
  }
  .card {
    width: 680px;
    height: 395px;
    background: var(--card);
    position: relative;
  }
  .card--front {
    display: flex;
    flex-direction: column;
    align-items: center;
    justify-content: center;
  }
  .wordmark {
    display: flex;
    align-items: center;
    gap: 16px;
    font-weight: 500;
    font-size: 78px;
    letter-spacing: -1px;
    color: var(--accent);
    line-height: 1;
  }
  .wordmark__square {
    width: 22px;
    height: 22px;
    background: var(--accent);
  }
  .front-url {
    margin-top: 46px;
    font-weight: 300;
    font-size: 17px;
    letter-spacing: 9px;
    color: var(--text);
  }
  .identity {
    position: absolute;
    right: 375px;
    top: 128px;
    text-align: right;
  }
  .identity__name {
    font-weight: 500;
    font-size: 25px;
    color: var(--accent);
    text-transform: uppercase;
  }
  .identity__role {
    margin-top: 4px;
    font-weight: 400;
    font-size: 19px;
    color: var(--muted);
    text-transform: uppercase;
  }
  .divider {
    position: absolute;
    left: 335px;
    top: 118px;
    width: 2px;
    height: 94px;
    background: var(--divider);
  }
  .contacts {
    position: absolute;
    left: 362px;
    top: 128px;
    list-style: none;
    font-size: 18px;
    line-height: 26px;
  }
  .contacts li { display: flex; align-items: center; gap: 10px; }
  .contacts svg, .address svg { flex: none; fill: var(--accent); }
  .address {
    position: absolute;
    left: 0; right: 0;
    bottom: 72px;
    display: flex;
    justify-content: center;
    align-items: center;
    gap: 8px;
    font-size: 19px;
  }
</style>
</head>
<body>
  <section class="card card--front">
    <div class="wordmark"><span class="wordmark__square"></span><span>ravelmere</span></div>
    <p class="front-url">www.ravelmere.eu</p>
  </section>

  <section class="card card--back">
    <div class="identity">
      <h1 class="identity__name">Markus Feldhofer</h1>
      <p class="identity__role">Geschäftsführer</p>
    </div>
    <div class="divider"></div>
    <ul class="contacts">
      <li>
        <svg width="16" height="16" viewBox="0 0 24 24" aria-hidden="true"><path d="M6.6 10.8a15 15 0 0 0 6.6 6.6l2.2-2.2a1 1 0 0 1 1-.25 11.4 11.4 0 0 0 3.6.57 1 1 0 0 1 1 1V20a1 1 0 0 1-1 1A17 17 0 0 1 3 4a1 1 0 0 1 1-1h3.5a1 1 0 0 1 1 1c0 1.25.2 2.45.57 3.57a1 1 0 0 1-.25 1z"/></svg>
        <span>+43 660 418 273 5</span>
      </li>
      <li>
        <svg width="16" height="16" viewBox="0 0 24 24" aria-hidden="true"><path d="M2 5h20v14H2zM3.5 6.5 12 12.5l8.5-6z" fill-rule="evenodd"/></svg>
        <span>m.feldhofer@ravelmere.eu</span>
      </li>
      <li>
        <svg width="16" height="16" viewBox="0 0 24 24" aria-hidden="true"><circle cx="12" cy="12" r="10"/><path d="M2 12h20M12 2c3 3 3 17 0 20M12 2c-3 3-3 17 0 20" stroke="#222224" stroke-width="1.6" fill="none"/></svg>
        <span>www.ravelmere.eu</span>
      </li>
    </ul>
    <p class="address">
      <svg width="16" height="20" viewBox="0 0 24 30" aria-hidden="true"><path d="M12 0a10 10 0 0 0-10 10c0 7.5 10 20 10 20s10-12.5 10-20A10 10 0 0 0 12 0zm0 14a4 4 0 1 1 0-8 4 4 0 0 1 0 8z"/></svg>
      <span>Birkengasse 9, A4560 kirchdorf</span>
    </p>
  </section>
</body>
</html>
```